Construction business card

I need a new business card, they can connect with my logo, brand.
What we do is residential house , design and build
I like: Navy blue / black
I attached our logo, brand,
and, some idea for business card.

```html
<!DOCTYPE html>
<html lang="en">
<head>
<meta charset="utf-8">
<title>Harlow Ridge Builders — Business Card</title>
<link href="https://fonts.googleapis.com/css2?family=Lato:wght@400;700&display=swap" rel="stylesheet">
<style>
  :root {
    --backdrop: #3a3b3e;
    --card: #0a0a0a;
    --ink: #ffffff;
    --accent: #3d84f0;
    --muted: #d9d9d9;
  }
  * { margin: 0; padding: 0; box-sizing: border-box; }
  html, body {
    width: 1200px;
    height: 915px;
    overflow: hidden;
    background: var(--backdrop);
    font-family: "Lato", Arial, sans-serif;
  }
  .sheet {
    width: 1200px;
    height: 915px;
    display: flex;
    flex-direction: column;
    align-items: center;
    justify-content: center;
    gap: 35px;
  }
  .card {
    position: relative;
    width: 700px;
    height: 400px;
    background: var(--card);
    border-radius: 26px;
    box-shadow: 0 10px 30px rgba(0,0,0,0.45);
    overflow: hidden;
  }

  /* Brand name block */
  .brand {
    display: flex;
    align-items: center;
    gap: 14px;
    color: var(--ink);
    font-weight: 700;
    text-transform: uppercase;
    letter-spacing: 0.06em;
    white-space: nowrap;
  }
  .brand-square {
    background: var(--accent);
    flex: none;
  }

  /* Front */
  .card-front {
    display: flex;
    align-items: center;
    justify-content: center;
  }
  .card-front .brand { font-size: 44px; }
  .card-front .brand-square { width: 30px; height: 30px; }

  /* Back */
  .card-back .brand {
    position: absolute;
    top: 58px;
    left: 50%;
    transform: translateX(-50%);
    font-size: 28px;
  }
  .card-back .brand-square { width: 20px; height: 20px; }

  .holder {
    position: absolute;
    top: 178px;
    right: 390px;
    text-align: right;
  }
  .holder-name {
    color: var(--accent);
    font-size: 28px;
    font-weight: 400;
    letter-spacing: 0.02em;
    text-transform: uppercase;
    white-space: nowrap;
  }
  .holder-role {
    color: var(--muted);
    font-size: 18px;
    margin-top: 4px;
  }

  .divider {
    position: absolute;
    left: 340px;
    top: 160px;
    width: 2px;
    height: 112px;
    background: var(--accent);
  }

  .contacts {
    position: absolute;
    left: 365px;
    top: 160px;
    list-style: none;
    display: flex;
    flex-direction: column;
    gap: 14px;
  }
  .contact {
    display: flex;
    align-items: center;
    gap: 12px;
    color: var(--ink);
    font-size: 18px;
  }
  .icon {
    width: 20px;
    height: 20px;
    flex: none;
    fill: var(--accent);
  }

  .address {
    position: absolute;
    left: 0;
    right: 0;
    bottom: 48px;
    display: flex;
    justify-content: center;
    align-items: center;
    gap: 10px;
    color: var(--ink);
    font-size: 19px;
  }
</style>
</head>
<body>
<main class="sheet">

  <section class="card card-front" aria-label="Card front">
    <div class="brand">
      <span class="brand-square"></span>
      <span class="brand-name">Harlow Ridge Builders</span>
    </div>
  </section>

  <section class="card card-back" aria-label="Card back">
    <div class="brand">
      <span class="brand-square"></span>
      <span class="brand-name">Harlow Ridge Builders</span>
    </div>

    <div class="holder">
      <p class="holder-name">Daniel Foster</p>
      <p class="holder-role">Owner</p>
    </div>

    <span class="divider"></span>

    <ul class="contacts">
      <li class="contact">
        <svg class="icon" viewBox="0 0 24 24" aria-hidden="true"><path d="M6.6 10.8a15.1 15.1 0 0 0 6.6 6.6l2.2-2.2a1 1 0 0 1 1-.25 11.4 11.4 0 0 0 3.6.57 1 1 0 0 1 1 1V20a1 1 0 0 1-1 1A17 17 0 0 1 3 4a1 1 0 0 1 1-1h3.5a1 1 0 0 1 1 1c0 1.25.2 2.45.57 3.57a1 1 0 0 1-.25 1z"/></svg>
        <span>0400 555 018</span>
      </li>
      <li class="contact">
        <svg class="icon" viewBox="0 0 24 24" aria-hidden="true"><path d="M2 5h20v14H2z M2 5l10 8 10-8" fill="none" stroke="var(--accent)" stroke-width="0"/><path d="M2 5h20l-10 8z"/><path d="M2 7.5l10 8 10-8V19H2z"/></svg>
        <span>hello@harlowridge.com</span>
      </li>
      <li class="contact">
        <svg class="icon" viewBox="0 0 24 24" aria-hidden="true"><circle cx="12" cy="12" r="10" fill="none" stroke="var(--accent)" stroke-width="2.4"/><path d="M12 2v20M2 12h20" stroke="var(--accent)" stroke-width="2"/><ellipse cx="12" cy="12" rx="4.5" ry="10" fill="none" stroke="var(--accent)" stroke-width="2"/></svg>
        <span>www.harlowridge.com</span>
      </li>
    </ul>

    <p class="address">
      <svg class="icon" viewBox="0 0 24 24" aria-hidden="true"><path d="M12 2a7 7 0 0 0-7 7c0 5.25 7 13 7 13s7-7.75 7-13a7 7 0 0 0-7-7zm0 9.5A2.5 2.5 0 1 1 12 6.5a2.5 2.5 0 0 1 0 5z"/></svg>
      <span>27 Elmstone Road, Springvale, Vic 3000</span>
    </p>
  </section>

</main>
</body>
</html>
```